Product Designer Business Card

Small product design, engineering and prototyping firm in need of a clean, professional business card design. To support our 3D design and drawing services, we offer 3D printing, molding, and casting of plastics, silicones, resins, etc. Our logo can still be modified/changed if necessary. The red/orange color is preferred, but may be substituted with blue or green, potentially. Either way, the colour of the logo should be match/compliment colors used throughout the design. One thought is to have the logo/contact info on one side, with the other side describing services offered, like with a small icon of 3D printer, molding, casting, and computer with a 3D model on-screen.
Industry/Entity Type
Mechanical Engineering
Contact Information for Business Card
Company: Kelvar Design
Phone: 613-582-9047
Email: mark@kelvardesign.ca

```html
<!DOCTYPE html>
<html lang="en">
<head>
<meta charset="utf-8">
<title>Kelvar Design – Business Card</title>
<link rel="stylesheet" href="https://fonts.googleapis.com/css2?family=Exo+2:wght@400;600;700&display=swap">
<style>
  :root {
    --backdrop: #3a3a3c;
    --blue-light: #0a96dc;
    --blue-deep: #0a5a94;
    --navy: #0d3a5c;
    --ink: #1c1c1c;
    --accent: #1a8fd6;
    --paper: #ffffff;
    --rule: #9aa3ab;
  }
  * { margin: 0; padding: 0; box-sizing: border-box; }
  html, body { width: 1200px; height: 1200px; overflow: hidden; }
  body {
    background: var(--backdrop);
    font-family: "Exo 2", sans-serif;
    position: relative;
  }
  .card {
    position: absolute;
    left: 250px;
    width: 700px;
    height: 400px;
    box-shadow: 0 12px 30px rgba(0,0,0,.35);
  }

  /* Services side */
  .card--services {
    top: 180px;
    background: linear-gradient(to bottom, var(--blue-light) 0%, var(--blue-deep) 100%);
    border-radius: 70px 0 70px 0;
    color: var(--paper);
  }
  .services-brand {
    position: absolute;
    top: 70px;
    left: 0; right: 0;
    display: flex;
    justify-content: center;
    align-items: center;
    gap: 18px;
    font-size: 84px;
    font-weight: 600;
    letter-spacing: 12px;
    line-height: 1;
  }
  .brand-dot {
    width: 46px; height: 46px;
    border-radius: 50%;
    background: var(--paper);
    flex: none;
  }
  .service-list {
    position: absolute;
    top: 225px;
    left: 70px; right: 70px;
    display: flex;
    justify-content: space-between;
    list-style: none;
  }
  .service {
    width: 120px;
    display: flex;
    flex-direction: column;
    align-items: center;
    gap: 14px;
    font-size: 19px;
    font-weight: 600;
    letter-spacing: .5px;
  }
  .service-icon {
    width: 76px; height: 68px;
    border-radius: 6px;
    background: rgba(255,255,255,.85);
  }

  /* Contact side */
  .card--contact {
    top: 620px;
    background: var(--paper);
    border-radius: 0 70px 0 70px;
  }
  .contact-brand {
    position: absolute;
    left: 60px;
    top: 138px;
    width: 290px;
    display: flex;
    align-items: flex-start;
    gap: 14px;
    color: var(--navy);
    font-size: 48px;
    font-weight: 600;
    line-height: 1.1;
  }
  .contact-brand .brand-dot {
    width: 34px; height: 34px;
    margin-top: 12px;
    background: var(--accent);
  }
  .brand-word { display: block; letter-spacing: 6px; }
  .brand-word--sub { letter-spacing: 14px; }
  .divider {
    position: absolute;
    left: 380px;
    top: 95px;
    width: 1px;
    height: 200px;
    background: var(--rule);
  }
  .contact-info {
    position: absolute;
    left: 405px;
    top: 100px;
  }
  .person-name {
    font-size: 34px;
    font-weight: 700;
    color: var(--accent);
    line-height: 1;
  }
  .person-role {
    font-size: 22px;
    font-weight: 400;
    color: var(--ink);
    margin-top: 4px;
  }
  .contact-lines {
    list-style: none;
    margin-top: 26px;
    display: flex;
    flex-direction: column;
    gap: 5px;
    font-size: 21px;
    color: var(--ink);
  }
  .contact-lines li { display: flex; align-items: center; gap: 9px; }
  .contact-lines svg { width: 20px; height: 20px; flex: none; }
  .web-accent { color: var(--accent); }
</style>
</head>
<body>

<section class="card card--services" aria-label="Card front, services">
  <div class="services-brand"><span class="brand-dot"></span>Kelvar</div>
  <ul class="service-list">
    <li class="service"><span class="service-icon" role="img" aria-label="3D printer icon"></span>3D Printer</li>
    <li class="service"><span class="service-icon" role="img" aria-label="Molding press icon"></span>Molding</li>
    <li class="service"><span class="service-icon" role="img" aria-label="Casting pour icon"></span>Casting</li>
    <li class="service"><span class="service-icon" role="img" aria-label="Monitor showing 3D model icon"></span>3d Model</li>
  </ul>
</section>

<section class="card card--contact" aria-label="Card back, contact">
  <div class="contact-brand">
    <span class="brand-dot"></span>
    <span>
      <span class="brand-word">Kelvar</span>
      <span class="brand-word brand-word--sub">Design</span>
    </span>
  </div>
  <div class="divider"></div>
  <div class="contact-info">
    <p class="person-name">Elias Brandt</p>
    <p class="person-role">Managing Director</p>
    <ul class="contact-lines">
      <li>
        <svg viewBox="0 0 20 20" aria-hidden="true"><rect x="1" y="1" width="18" height="18" rx="3" fill="none" stroke="#1a8fd6" stroke-width="1.6"/><path d="M7 5c-1 .6-1.6 1.6-1 3.2.8 2.3 2.6 4.3 5 5.4 1.3.6 2.4 0 3-1l-1.8-1.6-1.3.8c-1.2-.6-2.2-1.7-2.8-2.9l.8-1.3z" fill="#1a8fd6"/></svg>
        613-582-9047
      </li>
      <li>
        <svg viewBox="0 0 20 20" aria-hidden="true"><rect x="1" y="4" width="18" height="12" fill="#1a8fd6"/><path d="M1 4l9 7 9-7" fill="none" stroke="#fff" stroke-width="1.4"/></svg>
        mark@kelvardesign.ca
      </li>
      <li>
        <svg viewBox="0 0 20 20" aria-hidden="true"><g fill="none" stroke="#1a8fd6" stroke-width="1.5"><circle cx="10" cy="10" r="8.5"/><ellipse cx="10" cy="10" rx="3.8" ry="8.5"/><path d="M1.5 10h17M3 5.5h14M3 14.5h14"/></g></svg>
        <span>www.<span class="web-accent">kelvardesign</span>.ca</span>
      </li>
    </ul>
  </div>
</section>

</body>
</html>
```